New Business Card Design Project

We require a business card design for Vexalund, a newly established Indian company.
Our focus is on the development, manufacturing, and export of a diverse array of pharmaceutical products on a global scale. The card should convey a professional appearance, as our primary markets are in Africa, China, and Southeast Asian nations.
We envision a two-sided business card, with the reverse side dedicated to a logo set against a solid color or an elegantly designed pattern. The corners should be rounded. We would appreciate seeing both horizontal and vertical design options. We trust the designer to utilize their expertise in creating this design.

The content for the business card is included in the attached Word file.

Target Market(s)

Our primary markets are in Africa, China, and Southeast Asian, Latin America, Maldives, Sri Lanka

Industry/Entity Type

Pharmaceutical Manufacturing and Export

Contact Information for Business Card

Colors

Designer to choose colors to be used in the design.

Requirements
Must have
• The reverse side of the business card features solely the logo along with the tagline, "Care Beyond Borders."
Should not have
• The logo should not exceed two instances, encompassing both the front and back sides of the card.

```html
<!DOCTYPE html>
<html lang="en">
<head>
<meta charset="utf-8">
<title>Vexalund Business Card</title>
<link href="https://fonts.googleapis.com/css2?family=Montserrat:wght@600&family=Karla:wght@400&display=swap" rel="stylesheet">
<style>
  :root {
    --stage: #2a2a2a;
    --brand-blue: #2499d2;
    --band-blue: #2a8fc6;
    --brand-red: #d95442;
    --paper: #efefef;
    --paper-shade: #e2e2e2;
    --ink: #2b2b2b;
    --white: #f4f4f4;
  }
  * { margin: 0; padding: 0; box-sizing: border-box; }
  html, body { width: 1200px; height: 1138px; overflow: hidden; background: var(--stage); }
  .canvas { position: relative; width: 1200px; height: 1138px; }

  .card { position: absolute; border-radius: 20px; overflow: hidden; }

  /* Reverse side */
  .card-back {
    left: 274px; top: 185px; width: 623px; height: 377px;
    background: var(--brand-blue);
  }
  .back-brand {
    position: absolute; left: 0; right: 0; top: 224px;
    display: flex; justify-content: center; align-items: center; gap: 14px;
  }
  .brand-dot { border-radius: 50%; flex: none; }
  .back-brand .brand-dot { width: 22px; height: 22px; background: var(--white); }
  .back-name {
    font-family: "Montserrat", sans-serif; font-weight: 600;
    font-size: 60px; line-height: 1; color: var(--white); letter-spacing: -0.5px;
  }
  .back-tagline {
    position: absolute; left: 0; right: 0; top: 285px; text-align: center;
    font-family: "Karla", sans-serif; font-size: 13px; letter-spacing: 0.55em;
    color: var(--white); padding-left: 0.55em;
  }

  /* Front side */
  .card-front {
    left: 275px; top: 607px; width: 620px; height: 375px;
    background: linear-gradient(180deg, var(--paper) 0%, var(--paper) 55%, var(--paper-shade) 100%);
  }
  .front-dot {
    position: absolute; left: 58px; top: 64px;
    width: 36px; height: 36px; background: var(--brand-blue);
  }
  .front-name {
    position: absolute; left: 131px; top: 52px;
    font-family: "Montserrat", sans-serif; font-weight: 600;
    font-size: 55px; line-height: 1; color: var(--brand-blue); letter-spacing: -0.5px;
  }
  .person { position: absolute; left: 35px; top: 198px; }
  .person-name {
    font-family: "Montserrat", sans-serif; font-weight: 600;
    font-size: 23px; color: var(--brand-blue); line-height: 1.1;
  }
  .person-role {
    font-family: "Karla", sans-serif; font-size: 16px; color: var(--ink); margin-top: 5px;
  }
  .address {
    position: absolute; left: 35px; top: 292px; font-style: normal;
    font-family: "Karla", sans-serif; font-size: 16.5px; line-height: 22px; color: var(--ink);
  }
  .contacts { position: absolute; left: 342px; top: 198px; list-style: none; }
  .contacts li {
    display: flex; align-items: center; gap: 10px; height: 23px;
    font-family: "Karla", sans-serif; font-size: 17px; color: var(--ink);
  }
  .contacts svg { width: 14px; height: 14px; flex: none; }
  .footer-band { position: absolute; left: 0; bottom: 0; width: 620px; height: 47px; }
  .footer-tagline {
    position: absolute; left: 335px; top: 343px;
    font-family: "Karla", sans-serif; font-size: 16px; color: var(--white);
  }
</style>
</head>
<body>
<div class="canvas">

  <section class="card card-back" aria-label="Card reverse">
    <div class="back-brand">
      <span class="brand-dot"></span>
      <span class="back-name">Vexalund</span>
    </div>
    <p class="back-tagline">CARE BEYOND BORDERS</p>
  </section>

  <section class="card card-front" aria-label="Card front">
    <span class="brand-dot front-dot"></span>
    <span class="front-name">Vexalund</span>

    <div class="person">
      <h1 class="person-name">Rohan K. Mehtal</h1>
      <p class="person-role">CEO, Vexalund</p>
    </div>

    <ul class="contacts">
      <li>
        <svg viewBox="0 0 14 14"><path fill="#d95442" d="M1 5c0-2 2.5-3 6-3s6 1 6 3v1.5h-3V5H4v1.5H1z M3 7h8l1.5 5h-11z"/></svg>
        +91-9000412785
      </li>
      <li>
        <svg viewBox="0 0 14 14"><rect x="0.5" y="2.5" width="13" height="9" fill="#d95442"/><path d="M1 3l6 5 6-5M1 11l4.5-4M13 11l-4.5-4" stroke="#efefef" stroke-width="1.1" fill="none"/></svg>
        rmehtal@vexalund.com
      </li>
      <li>
        <svg viewBox="0 0 14 14"><circle cx="7" cy="7" r="6" fill="#d95442"/><path d="M1 7h12M7 1v12M2.5 4h9M2.5 10h9M7 1c-3 3-3 9 0 12M7 1c3 3 3 9 0 12" stroke="#efefef" stroke-width="0.8" fill="none"/></svg>
        https://vexalund.com
      </li>
    </ul>

    <address class="address">
      12, Suryoday Colony,<br>
      Kesarpur-441208 (INDIA)
    </address>

    <svg class="footer-band" viewBox="0 0 620 47" aria-hidden="true">
      <rect x="0" y="31" width="300" height="16" fill="var(--brand-red)"/>
      <path d="M263 47 L283 6 Q286 0 294 0 L620 0 L620 47 Z" fill="var(--band-blue)"/>
    </svg>
    <p class="footer-tagline">Care Beyond Borders.</p>
  </section>

</div>
</body>
</html>
```